Vehicle accessory sales website

We need a refreshed design for our vehicle accessory. This website is used to select vehicle year, make, model, trim and then displays products available for the vehicle you selected. The design needs to be responsive over mobile, tablet and desktop.

Current site: https://kelvorautoparts.example/vehicle-search/

We are only looking for an updated UI on the vehcile search function, not the website itself.

I want one full screen that is a Year, Make, Model and Trim Selection, this is a stamdalone page with no header, not a website page.

Then a screen that shows the vehicle selected at the top (Not a vehicle image) and the available product categories.

Then a screen that still shows the products avaiable after selecting the category

Then a product pop up

Then a checkout screen

Target Market(s)

Car dealership customers and salespeople

Industry/Entity Type

Automotive accessories

Number of Pages Required

3 page

Requirements
Must have
• Vehicle selection page, main category page, product page after category has been selected, product pop up and checkout screen

```html
<!DOCTYPE html>
<html lang="en">
<head>
<meta charset="UTF-8">
<title>Select Your Vehicle – Kelvor Auto Parts</title>
<link rel="stylesheet" href="https://fonts.googleapis.com/css2?family=Orbitron:wght@900&family=Montserrat:wght@400;500;700&display=swap">
<style>
  :root {
    --backdrop-top: #5f86b8;
    --backdrop-bottom: #6b7466;
    --panel: rgba(14, 14, 14, 0.84);
    --text: #ffffff;
    --field-border: #ffffff;
    --accent: #5cb85c;
  }
  * { box-sizing: border-box; margin: 0; padding: 0; }
  html, body { width: 1200px; height: 645px; overflow: hidden; }
  body { font-family: "Montserrat", sans-serif; color: var(--text); }

  .stage { position: relative; width: 1200px; height: 645px; overflow: hidden; }

  .backdrop {
    position: absolute; inset: 0;
    background: linear-gradient(180deg, var(--backdrop-top) 0%, var(--backdrop-bottom) 100%);
  }

  .vehicle-panel {
    position: absolute; left: 369px; top: 48px;
    width: 457px; height: 542px;
    background: var(--panel);
    border-radius: 8px;
  }

  .panel-title {
    position: absolute; left: 0; right: 0; top: 32px;
    text-align: center;
    font-family: "Orbitron", sans-serif;
    font-weight: 900; font-size: 23px; letter-spacing: 2px;
    line-height: 28px;
    text-transform: uppercase;
  }

  .field-label {
    position: absolute; left: 35px;
    font-size: 15.5px; font-weight: 500;
  }

  .field-select {
    position: absolute; left: 28px; width: 402px; height: 46px;
    border: 2px solid var(--field-border); border-radius: 7px;
    display: flex; align-items: center; padding-left: 11px;
    font-size: 13px; font-weight: 400;
  }
  .field-select .caret {
    position: absolute; right: 17px; top: 50%;
    width: 16px; height: 9px; margin-top: -4px;
  }

  .view-button {
    position: absolute; left: 124px; top: 461px;
    width: 205px; height: 46px;
    background: var(--accent); border-radius: 6px;
    display: flex; align-items: center; justify-content: center; gap: 9px;
    font-size: 15.5px; font-weight: 700;
  }
  .view-button svg { width: 24px; height: 16px; }
</style>
</head>
<body>
<main class="stage">
  <div class="backdrop" role="img" aria-label="Photo of an open highway through green grassland under a blue cloudy sky"></div>

  <section class="vehicle-panel" aria-labelledby="panel-title">
    <h1 class="panel-title" id="panel-title">Select Your Vehicle</h1>

    <span class="field-label" style="top:84px">Make</span>
    <div class="field-select" style="top:110px">Varden
      <svg class="caret" viewBox="0 0 16 9"><path d="M0 0h16L8 9z" fill="#fff"/></svg>
    </div>

    <span class="field-label" style="top:174px">Year Of Manufacturing</span>
    <div class="field-select" style="top:201px">2022
      <svg class="caret" viewBox="0 0 16 9"><path d="M0 0h16L8 9z" fill="#fff"/></svg>
    </div>

    <span class="field-label" style="top:265px">Model</span>
    <div class="field-select" style="top:291px">V7
      <svg class="caret" viewBox="0 0 16 9"><path d="M0 0h16L8 9z" fill="#fff"/></svg>
    </div>

    <span class="field-label" style="top:358px">Trim</span>
    <div class="field-select" style="top:384px">Premium
      <svg class="caret" viewBox="0 0 16 9"><path d="M0 0h16L8 9z" fill="#fff"/></svg>
    </div>

    <div class="view-button">View Accessories
      <svg viewBox="0 0 24 16" fill="none" stroke="#fff" stroke-width="2" stroke-linecap="round" stroke-linejoin="round"><path d="M1 8h21M15 1l7 7-7 7"/></svg>
    </div>
  </section>
</main>
</body>
</html>
```